Building company buisness cards

We are looking for a sharp modern new look for our business cards.
We are a New Zealand based company that specialises in house and land packages.
We have attached a photo of the current logo and would like to see if it can be improved somehow if needed.
We are open to any colours but we have chosen green at this stage.
Feel free to change the font and make the logo smarter looking.
Play with the colours and see what looks best.

We want a card that looks so good know one will want to throw it away!

Target Market(s)

Home buyers

Industry/Entity Type

Building

Contact Information for Business Card

Derek Tolvane
0217394062
dtolvane@quillmarkhomesteads.co.nz
quillmarkhomesteads.co.nz

Font styles to use
Serif
Sans Serif

Colors

Designer to choose colors to be used in the design.

Requirements
Must have
• Logo and company name on one side, details on the other side
Nice to have
• Color codes for the original green are HEX #4a8028, RGB(74,128,40), CMYK(42,0,69,50)
• Round corners, Raised and/or spot UV

```html
<!DOCTYPE html>
<html lang="en">
<head>
<meta charset="utf-8">
<title>Quillmark Homesteads – Business Cards</title>
<link rel="stylesheet" href="https://fonts.googleapis.com/css2?family=Montserrat:wght@500;800&family=Roboto:wght@400&display=swap">
<style>
  :root {
    --brand-green: #5e8244;
    --paper: #ffffff;
    --ink: #1c1c1c;
    --backdrop: #e4e0d8;
  }
  * { margin: 0; padding: 0; box-sizing: border-box; }
  html, body { width: 1200px; height: 1200px; overflow: hidden; }
  body { background: var(--backdrop); position: relative; font-family: "Roboto", sans-serif; }

  .card { position: absolute; left: 229px; width: 742px; height: 424px; }
  .card-front { top: 147px; background: var(--brand-green); }
  .card-back { top: 640px; background: var(--paper); }

  .brand-dot { border-radius: 50%; flex: none; }

  /* front: mark beside wordmark */
  .front-lockup {
    position: absolute; top: 146px; left: 0; right: 0;
    display: flex; justify-content: center; align-items: center; gap: 20px;
  }
  .front-lockup .brand-dot { width: 96px; height: 96px; background: var(--paper); }

  .wordmark {
    font-family: "Montserrat", sans-serif; font-weight: 800;
    letter-spacing: -0.5px; line-height: 1;
  }
  .card-front .wordmark { color: var(--paper); text-align: left; }
  .card-front .wordmark-top { font-size: 32px; display: block; margin-left: 34px; }
  .card-front .wordmark-bottom { font-size: 46px; display: block; margin-top: 4px; }

  /* back: mark above wordmark */
  .back-lockup {
    position: absolute; top: 38px; left: 0; right: 0;
    display: flex; flex-direction: column; align-items: center;
  }
  .back-lockup .brand-dot { width: 62px; height: 62px; background: var(--brand-green); }
  .card-back .wordmark { color: var(--brand-green); text-align: center; margin-top: 12px; }
  .card-back .wordmark-top { font-size: 29px; display: block; }
  .card-back .wordmark-bottom { font-size: 41px; display: block; margin-top: 3px; }
  .wordmark-rule {
    position: absolute; top: 197px; left: 336px; width: 70px; height: 1px;
    background: var(--brand-green);
  }

  .holder-row {
    position: absolute; left: 53px; right: 51px; top: 262px;
    display: flex; align-items: flex-end;
  }
  .holder-name {
    font-family: "Montserrat", sans-serif; font-weight: 500;
    font-size: 27px; letter-spacing: 1px; color: var(--brand-green);
    line-height: 1; white-space: nowrap; flex: none;
  }
  .holder-rule {
    flex: 1; margin-left: 10px; height: 1px; margin-bottom: 2px;
    background: var(--brand-green); position: relative;
  }
  .holder-title {
    position: absolute; right: 0; bottom: 8px;
    font-size: 17px; letter-spacing: 1px; color: var(--ink); line-height: 1;
  }

  .contact-list { position: absolute; right: 51px; top: 316px; list-style: none; }
  .contact-item {
    display: flex; justify-content: flex-end; align-items: center;
    height: 26px; font-size: 16.5px; letter-spacing: 1px; color: var(--ink);
  }
  .contact-item svg { width: 14px; height: 14px; margin-left: 14px; fill: var(--brand-green); }

  .card-band {
    position: absolute; left: 0; bottom: 0; width: 100%; height: 19px;
    background: var(--brand-green);
  }
</style>
</head>
<body>
  <section class="card card-front" aria-label="Card front">
    <div class="front-lockup">
      <span class="brand-dot" aria-hidden="true"></span>
      <h1 class="wordmark">
        <span class="wordmark-top">quillmark</span>
        <span class="wordmark-bottom">house plans.</span>
      </h1>
    </div>
  </section>

  <section class="card card-back" aria-label="Card back">
    <div class="back-lockup">
      <span class="brand-dot" aria-hidden="true"></span>
      <h2 class="wordmark">
        <span class="wordmark-top">quillmark</span>
        <span class="wordmark-bottom">homesteads.</span>
      </h2>
    </div>
    <div class="wordmark-rule"></div>

    <div class="holder-row">
      <p class="holder-name">DEREK TOLVANE</p>
      <div class="holder-rule"><p class="holder-title">Director</p></div>
    </div>

    <ul class="contact-list">
      <li class="contact-item">0217394062
        <svg viewBox="0 0 24 24" aria-hidden="true"><path d="M6.6 10.8a15.1 15.1 0 0 0 6.6 6.6l2.2-2.2c.3-.3.7-.4 1-.2 1.1.4 2.3.6 3.6.6.6 0 1 .4 1 1V20c0 .6-.4 1-1 1A17 17 0 0 1 3 4c0-.6.4-1 1-1h3.5c.6 0 1 .4 1 1 0 1.3.2 2.5.6 3.6.1.3 0 .7-.2 1z"/></svg>
      </li>
      <li class="contact-item">dtolvane@quillmarkhomesteads.co.nz
        <svg viewBox="0 0 24 24" aria-hidden="true"><path d="M2 5h20v2.2l-10 6-10-6z"/><path d="M2 9.5l10 6 10-6V19H2z"/></svg>
      </li>
      <li class="contact-item">www.quillmarkhomesteads.co.nz
        <svg viewBox="0 0 24 24" aria-hidden="true"><path d="M12 2a10 10 0 1 0 0 20 10 10 0 0 0 0-20zm0 2c.9 0 2 1.6 2.6 4H9.4C10 5.6 11.1 4 12 4zM4.4 10h4.7a19 19 0 0 0 0 4H4.4a8 8 0 0 1 0-4zm.8 6h4.2c.3 1.3.8 2.5 1.3 3.4A8 8 0 0 1 5.2 16zm4-8H5.2a8 8 0 0 1 5.5-3.4c-.5.9-1 2.1-1.3 3.4zM12 20c-.9 0-2-1.6-2.6-4h5.2c-.6 2.4-1.7 4-2.6 4zm2.9-6h-5.8a17 17 0 0 1 0-4h5.8a17 17 0 0 1 0 4zm.4 5.4c.5-.9 1-2.1 1.3-3.4h4.2a8 8 0 0 1-5.5 3.4zM16.9 14a19 19 0 0 0 0-4h4.7a8 8 0 0 1 0 4zm-.3-6c-.3-1.3-.8-2.5-1.3-3.4A8 8 0 0 1 20.8 8z"/></svg>
      </li>
    </ul>

    <div class="card-band"></div>
  </section>
</body>
</html>
```